PDF flyer for our companies' two main products: Food processing machines.

PDF flyer with showcasing two products. Flyer can be one page per product, or both products on the same page.

Product #1: Labeled "Ribbon blenders".
Showing a photo of the machine, and the details/features offered with that machine. Product description must also say: "Sizes available; 2 Cu Ft. - 450 Cu Ft."

Product #2: Labeled: " Auger hoppers / Screw feeders"
Showing a photo of the machine, and the details/features offered with that machine.

SEE UPLOADED IMAGES; "Ribbon Blenders EXAMPLE FLYER".
& "Auger Hoppers / Screw Conveyors EXAMPLE FLYER" for a rough idea of what we are looking for.

Target Market(s)

Copackers, Packing houses, Food manufacturers, protein powder producers,

Industry/Entity Type

Commercial Food processing / packing / mixing equipment

Font styles to use
Serif

Colors
0054AA
0677BA
7BADD7
CADEEF
E8F1F8

Requirements
Must have
• Company logo on top of flyer.
Nice to have
• I would like for the flyer to show some stock images of common ingredients, similar to the images uploaded.
Should not have
• Pictures with background. Backgrounds must be removed from provides photos. "clipping path"

```html
<!DOCTYPE html>
<html lang="en">
<head>
<meta charset="utf-8">
<title>Steelcore – Ribbon Blenders &amp; Auger Hoppers</title>
<link href="https://fonts.googleapis.com/css2?family=Montserrat:wght@400;500;700;800&family=Oswald:wght@500;600&display=swap" rel="stylesheet">
<style>
:root{
  --blue-deep:#0054AA;
  --blue:#0677BA;
  --blue-mid:#7BADD7;
  --blue-light:#CADEEF;
  --blue-pale:#E8F1F8;
  --ink:#1c1c1c;
  --text:#3a3a3a;
  --paper:#ffffff;
  --stage:#2a2a2a;
}
*{box-sizing:border-box;margin:0;padding:0}
html,body{width:1200px;height:801px;overflow:hidden;background:var(--stage)}
body{font-family:"Montserrat",sans-serif;color:var(--text)}
.spread{position:absolute;left:20px;top:20px;width:1160px;height:761px;display:flex}
.page{position:relative;width:580px;height:761px;background:var(--paper);overflow:hidden}
.page + .page{border-left:1px solid #ddd}
.band{position:absolute;left:0;width:580px}
.band--top{top:0;height:200px}
.band--bottom{bottom:0;height:90px}
.brand{position:absolute;top:22px;display:flex;align-items:center;gap:7px;font-weight:800;font-size:17px;letter-spacing:2px;color:var(--paper)}
.brand__dot{width:12px;height:12px;border-radius:50%;background:var(--blue-mid)}
.page--blenders .brand{left:28px}
.page--augers .brand{right:28px}
.product-card{position:absolute;background:var(--paper);box-shadow:0 4px 16px rgba(0,0,0,.18);padding:12px}
.product-card .photo{width:100%;height:100%;border-radius:3px;background:linear-gradient(160deg,#eef0f2 0%,#c4c9ce 40%,#8f969d 70%,#dfe2e5 100%)}
.ingredients{position:absolute;border-radius:8px;background:linear-gradient(100deg,#e39a2e 0%,#c8a15a 22%,#b83a2a 45%,#8a6a45 70%,#d9b25a 100%)}
.title{position:absolute;font-weight:800;color:var(--ink);text-transform:uppercase;letter-spacing:.5px}
.subtitle{position:absolute;font-weight:700;font-size:9.5px;color:var(--blue)}
.heading{position:absolute;font-weight:800;font-size:13px;color:var(--ink);text-transform:uppercase;letter-spacing:.5px}
.list{position:absolute;list-style:none;font-size:8.4px;line-height:12.5px;color:var(--text)}
.list li{position:relative;padding-left:13px}
.list li::before{content:"";position:absolute;left:0;top:3px;width:7px;height:7px;border-radius:50%;background:var(--blue-deep)}
.spec{position:absolute;border-collapse:collapse;font-size:7px;color:var(--ink)}
.spec td,.spec th{border:1px solid #333;padding:1px 3px;text-align:left;white-space:nowrap}
.spec th{font-weight:700}
.spec--blenders{left:30px;top:525px;width:520px}
.spec--blenders td:first-child{font-weight:500}
.spec--augers{left:30px;top:510px;width:520px;font-family:"Oswald",sans-serif;font-size:10px;font-weight:500;letter-spacing:.3px}
.spec--augers td{border:1.6px solid #000;padding:2px 5px;text-transform:uppercase}
.contact{position:absolute;bottom:14px;display:flex;gap:26px;font-size:8.5px;font-weight:500;color:var(--paper)}
.contact span{display:flex;align-items:center;gap:6px}
.contact svg{width:11px;height:11px}
.page--blenders .contact{left:200px}
.page--augers .contact{right:40px}
</style>
</head>
<body>
<main class="spread">

  <section class="page page--blenders">
    <svg class="band band--top" viewBox="0 0 580 200">
      <defs>
        <linearGradient id="factoryA" x1="0" x2="1" y1="0" y2="1">
          <stop offset="0" stop-color="#8d9196"/><stop offset=".5" stop-color="#c3c6c9"/><stop offset="1" stop-color="#7b7f84"/>
        </linearGradient>
      </defs>
      <polygon points="0,0 580,0 580,95 0,185" fill="url(#factoryA)" role="img" aria-label="Ribbon blender installed in a production room"/>
      <polygon points="0,185 580,95 580,110 420,150 0,200" fill="var(--blue-deep)"/>
      <polygon points="580,110 580,140 470,160" fill="var(--blue)"/>
    </svg>
    <div class="brand"><span class="brand__dot"></span>STEELCORE</div>

    <div class="product-card" style="left:40px;top:180px;width:210px;height:170px">
      <div class="photo" role="img" aria-label="Stainless steel ribbon blender on a wheeled frame"></div>
    </div>

    <h1 class="title" style="left:285px;top:198px;font-size:15px">Ribbon Blenders</h1>
    <p class="subtitle" style="left:285px;top:220px">Sizes available; 2 Cu Ft. - 450 Cu Ft.</p>
    <div class="ingredients" role="img" aria-label="Spices and seeds in wooden spoons and bowls" style="left:285px;top:240px;width:270px;height:90px"></div>

    <h2 class="heading" style="left:30px;top:362px">Standard Features</h2>
    <ul class="list" style="left:30px;top:381px;width:255px">
      <li>304 stainless steel construction.</li>
      <li>Pre-wired control panels with; batch timer, on/off switch, emergency stop button.</li>
      <li>Food grade compression shaft seals.</li>
      <li>Safety sensor on lid for automatic shutoff when opened.</li>
      <li>Air actuated discharge valve.</li>
      <li>1 piece hinged lid with safety grating.</li>
      <li>Power options; 220v/480v.</li>
      <li>24" standard discharge height.</li>
      <li>Castor wheels on 53cf units and smaller</li>
    </ul>

    <h2 class="heading" style="left:300px;top:352px">Options</h2>
    <ul class="list" style="left:300px;top:371px;width:260px">
      <li>Dual hinged lids available on custom orders.</li>
      <li>Knife gate style discharge available on custom orders.</li>
      <li>Air purge seals available on custom orders.</li>
      <li>316 stainless material available on custom orders.</li>
      <li>Custom height modification.</li>
      <li>Liquid spray systems</li>
      <li>(VFD) Variable Frequency Drives</li>
      <li>Leg extensions</li>
    </ul>

    <table class="spec spec--blenders">
      <tr><th>Model Size</th><th>5cf</th><th>7CF</th><th>10.5CF</th><th>17.5CF</th><th>35CF</th><th>53CF</th><th>70.5CF</th><th>106CF</th></tr>
      <tr><td>Working Liters</td><td>120L</td><td>200L</td><td>300L</td><td>500L</td><td>1000L</td><td>1500L</td><td>2000L</td><td>3000L</td></tr>
      <tr><td>Fill Capacity</td><td>5CF / 150L</td><td>9CF / 250L</td><td>13CF / 375L</td><td>22CF / 625L</td><td>44CF / 1250L</td><td>66CF / 1875L</td><td>88CF / 2500L</td><td>132CF / 3750L</td></tr>
      <tr><td>Weight</td><td>440lbs</td><td>550lbs</td><td>770lbs</td><td>1212lbs</td><td>1874lbs</td><td>2645lbs</td><td>3527lbs</td><td>5511lbs</td></tr>
      <tr><td>Motor Size</td><td>4hp</td><td>5.3hp</td><td>6.7hp</td><td>10hp</td><td>14.75hp</td><td>20hp</td><td>25hp</td><td>30hp</td></tr>
      <tr><td>Total Length</td><td>50"</td><td>53.5"</td><td>63"</td><td>72"</td><td>94"</td><td>102"</td><td>131.5"</td><td>157.5"</td></tr>
      <tr><td>Total Width</td><td>28"</td><td>34"</td><td>41.5"</td><td>45"</td><td>52"</td><td>66"</td><td>52.5"</td><td>54"</td></tr>
      <tr><td>Total Height</td><td>66"</td><td>69"</td><td>71"</td><td>82"</td><td>87"</td><td>95"</td><td>76"</td><td>110"</td></tr>
      <tr><td>Tub Length</td><td>31.5"</td><td>35.5"</td><td>41"</td><td>47"</td><td>59"</td><td>70"</td><td>75"</td><td>100"</td></tr>
      <tr><td>Tub Width</td><td>16.5"</td><td>22"</td><td>25"</td><td>27.5"</td><td>35.5"</td><td>39"</td><td>48"</td><td>48"</td></tr>
      <tr><td>Tub Height</td><td>20.5"</td><td>26"</td><td>28"</td><td>33"</td><td>41"</td><td>46"</td><td>51"</td><td>53"</td></tr>
      <tr><td>Shaft Diameter</td><td>2"</td><td>2-1/4"</td><td>2-5/8"</td><td>3"</td><td>3.5"</td><td>4"</td><td>4"</td><td>5-1/4"</td></tr>
      <tr><td>Tub Thickness</td><td>3mm</td><td>3mm</td><td>3mm</td><td>4mm</td><td>4mm</td><td>5mm</td><td>5mm</td><td>6mm</td></tr>
      <tr><td>Ribbon Thickness</td><td>6mm</td><td>8mm</td><td>8mm</td><td>8mm</td><td>10mm</td><td>12mm</td><td>12mm</td><td>14mm</td></tr>
      <tr><td>Max RPM</td><td>46 rpm</td><td>46 rpm</td><td>46 rpm</td><td>46 rpm</td><td>30 rpm</td><td>31 rpm</td><td>32 rpm</td><td>33 rpm</td></tr>
    </table>

    <svg class="band band--bottom" viewBox="0 0 580 90" aria-hidden="true">
      <polygon points="0,40 0,20 70,60" fill="var(--blue)"/>
      <polygon points="0,70 580,45 580,90 0,90" fill="var(--blue-deep)"/>
    </svg>
    <div class="contact">
      <span><svg viewBox="0 0 12 12"><path d="M3 1l2 2.5-1 1.2a6 6 0 0 0 3.3 3.3l1.2-1L11 9l-1.3 1.8C6 11 1 6 1.2 2.3z" fill="#fff"/></svg>+1 (555) 014 2090</span>
      <span><svg viewBox="0 0 12 12"><rect x="1" y="2.5" width="10" height="7" rx="1" fill="none" stroke="#fff"/><path d="M1.5 3l4.5 3.5L10.5 3" fill="none" stroke="#fff"/></svg>info@steelcoremix.com</span>
    </div>
  </section>

  <section class="page page--augers">
    <svg class="band band--top" viewBox="0 0 580 200">
      <defs>
        <linearGradient id="factoryB" x1="0" x2="1" y1="0" y2="1">
          <stop offset="0" stop-color="#d9d9d6"/><stop offset=".6" stop-color="#b9bab8"/><stop offset="1" stop-color="#8e9092"/>
        </linearGradient>
      </defs>
      <polygon points="0,0 580,0 580,45 0,165" fill="url(#factoryB)" role="img" aria-label="Auger hopper with inclined screw feeder in a warehouse"/>
      <polygon points="0,165 580,45 580,62 110,160 60,175 0,185" fill="var(--blue-deep)"/>
      <polygon points="0,185 60,175 20,200 0,200" fill="var(--blue)"/>
    </svg>
    <div class="brand"><span class="brand__dot"></span>STEELCORE</div>

    <div class="product-card" style="left:40px;top:190px;width:200px;height:160px">
      <div class="photo" role="img" aria-label="Auger hopper with inclined screw feeder tube"></div>
    </div>

    <h1 class="title" style="left:262px;top:175px;font-size:13.5px">Auger Hoppers / Screw Feeders</h1>
    <div class="ingredients" role="img" aria-label="Bowls of ground spices, powder pile and peppercorns" style="left:262px;top:200px;width:290px;height:90px"></div>

    <h2 class="heading" style="left:300px;top:305px">Options</h2>
    <ul class="list" style="left:300px;top:324px;width:260px">
      <li>Square or round hopper. 3.5cf and 7cf hoppers are standard.</li>
      <li>Custom hoppers up to 200cf.</li>
      <li>VFD Variable Frequency Drive).</li>
      <li>Clamshell Auger tube for easy cleanout.</li>
      <li>316 Stainless steel construction.</li>
    </ul>

    <h2 class="heading" style="left:40px;top:372px">Standard Features</h2>
    <ul class="list" style="left:40px;top:391px;width:240px">
      <li>Direct Drive.</li>
      <li>304 Stainless steel construction.</li>
      <li>Stainless steel safety grating.</li>
      <li>Pre-wired control panel.</li>
      <li>Electric Vibrator.</li>
      <li>Castor Wheels</li>
    </ul>

    <table class="spec spec--augers">
      <tr><td>Model</td><td>AH-A2</td><td>AH-A3</td><td>AH-A5</td><td>AH-A7</td><td>AH-A8</td><td>AH-A12</td></tr>
      <tr><td>Feeding Rate</td><td>2m³/hr</td><td>3m³/hr</td><td>5m³/hr</td><td>7m³/hr</td><td>8m³/hr</td><td>12m³/hr</td></tr>
      <tr><td>Pipe Diameter</td><td>4"</td><td>4-1/2"</td><td>5-1/2"</td><td>6-1/4"</td><td>6-1/2"</td><td>8-1/2"</td></tr>
      <tr><td>Hopper Vol.</td><td colspan="3">3.5CF</td><td colspan="3">7CF</td></tr>
      <tr><td>Dimensions</td><td colspan="3">28.6"x24.4"x31.5"</td><td colspan="3">40" x 32" x 35"</td></tr>
      <tr><td>Total Weight</td><td>221LBS</td><td>287LBS</td><td>397LBS</td><td>441LBS</td><td>485LBS</td><td>596LBS</td></tr>
      <tr><td>Charging Height</td><td colspan="6">Standard 72 inches. (40" - 196" available)</td></tr>
      <tr><td>Charging Angle</td><td colspan="6">Standard 45° (30°-60° available)</td></tr>
    </table>

    <svg class="band band--bottom" viewBox="0 0 580 90" aria-hidden="true">
      <polygon points="0,90 580,30 580,90" fill="var(--blue-deep)"/>
      <polygon points="540,0 580,0 580,30 500,40" fill="var(--blue)"/>
    </svg>
    <div class="contact">
      <span><svg viewBox="0 0 12 12"><path d="M3 1l2 2.5-1 1.2a6 6 0 0 0 3.3 3.3l1.2-1L11 9l-1.3 1.8C6 11 1 6 1.2 2.3z" fill="#fff"/></svg>+1 (555) 014 2090</span>
      <span><svg viewBox="0 0 12 12"><rect x="1" y="2.5" width="10" height="7" rx="1" fill="none" stroke="#fff"/><path d="M1.5 3l4.5 3.5L10.5 3" fill="none" stroke="#fff"/></svg>info@steelcoremix.com</span>
    </div>
  </section>

</main>
</body>
</html>
```